full stationary design for a modern sleek design company

we are a design company that does modern minimalistic interior design works as well as other design services for high end clients.
we need a full stationary design including and not limited to (double sided business card, letter head, envelopes, documents folder...etc) that reflects the modern style design we do.
sleek modern and minimalistic is the requirements.
Updates

please use the latest attached files as there was a slight modification on the logo Added Wednesday, March 1, 2017

minor update on the logo files in JPG and PSD has been updated kindly follow the new attachments. Added Thursday, March 2, 2017

Target Market(s)

modern minimalist clients

Industry/Entity Type

Design Agency

Requirements
Must have
• the logo
Nice to have
• i like the colors in the colored 3D logo attached
Should not have
• too many colors

```html
<!DOCTYPE html>
<html lang="en">
<head>
<meta charset="utf-8">
<title>Form Atelier – Business Card</title>
<link rel="stylesheet" href="https://fonts.googleapis.com/css2?family=Open+Sans:wght@400;600&display=swap">
<style>
  :root {
    --page-bg: #e4e1de;
    --card-dark: #1d1d1f;
    --card-dark-mid: #3a3a3c;
    --accent: #e8731f;
    --accent-deep: #c2520f;
    --accent-light: #f08a35;
    --text-light: #f1f1f1;
    --ring: #e9e9e9;
    --logo-ink: #2a2a2a;
  }
  html, body {
    margin: 0;
    width: 1200px;
    height: 969px;
    overflow: hidden;
    background: var(--page-bg);
  }
  .business-card {
    position: absolute;
    left: 100px;
    top: 200px;
    width: 1000px;
    height: 569px;
    border-radius: 34px;
    overflow: hidden;
    box-shadow: 0 18px 40px rgba(0,0,0,0.25);
  }
  .business-card svg { display: block; }
  .card-text { font-family: "Open Sans", Arial, sans-serif; }
  .holder-name { fill: var(--accent); font-size: 33px; font-weight: 600; letter-spacing: 0.5px; }
  .holder-role { fill: var(--text-light); font-size: 25px; font-weight: 400; }
  .contact-line { fill: var(--text-light); font-size: 25px; font-weight: 400; }
  .contact-icon { fill: var(--accent); }
  .brand-name { fill: var(--logo-ink); font-size: 44px; font-weight: 600; letter-spacing: 3px; }
  .brand-mark { fill: var(--logo-ink); }
</style>
</head>
<body>
<div class="business-card">
  <svg width="1000" height="569" viewBox="0 0 1000 569" xmlns="http://www.w3.org/2000/svg">
    <defs>
      <linearGradient id="darkPanel" x1="0" y1="0" x2="1" y2="0">
        <stop offset="0" stop-color="#2c2c2e"/>
        <stop offset="0.55" stop-color="#3e3e40"/>
        <stop offset="1" stop-color="#161618"/>
      </linearGradient>
      <radialGradient id="accentFill" cx="0.55" cy="0.45" r="0.7">
        <stop offset="0" stop-color="#f08a35"/>
        <stop offset="0.6" stop-color="#e0681b"/>
        <stop offset="1" stop-color="#b94c0e"/>
      </radialGradient>
    </defs>

    <!-- dark panel -->
    <rect class="card-panel" width="1000" height="569" fill="url(#darkPanel)"/>

    <!-- accent disc with light ring -->
    <circle class="accent-ring" cx="830" cy="284" r="400" fill="var(--ring)"/>
    <circle class="accent-disc" cx="830" cy="284" r="390" fill="url(#accentFill)" role="img" aria-label="Frosted orange translucent panel"/>

    <!-- holder details -->
    <g class="card-text">
      <text class="holder-name" x="54" y="145">MARA LINDEN</text>
      <text class="holder-role" x="54" y="183">CEO&amp;Founder</text>

      <text class="contact-line" x="54" y="234">2140 Alder Court</text>
      <text class="contact-line" x="54" y="270">Juneau, Alaska 99801</text>

      <text class="contact-line" x="94" y="315">(555) 210 4817</text>
      <text class="contact-line" x="94" y="353">(555) 730 2956</text>
      <text class="contact-line" x="94" y="391">mara@formatelier.com</text>
      <text class="contact-line" x="94" y="429">www.formatelier.com</text>
    </g>

    <!-- contact icons -->
    <g class="contact-icon">
      <!-- phone -->
      <path d="M60 296 q-3 4 0 9 q6 9 14 14 q5 2 8 -1 l3 -3 q1 -2 -1 -3 l-5 -3 q-2 -1 -3 1 l-2 2 q-5 -3 -8 -8 l2 -2 q2 -1 1 -3 l-3 -5 q-1 -2 -3 -1 z"/>
      <!-- mobile -->
      <path d="M63 332 h14 a3 3 0 0 1 3 3 v22 a3 3 0 0 1 -3 3 h-14 a3 3 0 0 1 -3 -3 v-22 a3 3 0 0 1 3 -3 z M64 336 v17 h12 v-17 z"/>
      <!-- envelope -->
      <path d="M58 376 h24 v16 h-24 z M60 378 l10 8 l10 -8 z" fill-rule="evenodd"/>
      <!-- globe -->
      <circle cx="70" cy="421" r="11"/>
      <path d="M59 421 h22 M70 410 v22" stroke="#2c2c2e" stroke-width="1.8" fill="none"/>
      <ellipse cx="70" cy="421" rx="5" ry="11" stroke="#2c2c2e" stroke-width="1.8" fill="none"/>
    </g>

    <!-- brand name -->
    <g class="brand">
      <rect class="brand-mark" x="532" y="262" width="30" height="30"/>
      <text class="card-text brand-name" x="578" y="292">FORM ATELIER</text>
    </g>
  </svg>
</div>
</body>
</html>
```